Defense Attorney Business Card Design Project/ Stationary

I am looking for a distinctive business card design for my solo law practice.
I practice criminal defense, both juvenile and adult, including DUI. I am a very experienced attorney with prior military experience. The design should convey a traditional, old school flair, but not be too stodgy or uptight. Some color. My logo should appear.
Updates

Project Deadline Extended Reason: I misunderstood how this project works and I was not prepared with my logo when this project ran the first time. Added Thursday, November 13, 2014

Project Deadline Extended
Reason: I was sent overseas on military duty last year, which interrupted this project. Thank you for your participation... I hope we can get this done this week! Thank you, Neil

Target Market(s)

Regular everyday people looking for strong, knowledgeable, authoritative representation while they are faced with criminal charges. Many have never been charged with a crime before. A reassuring air is therefore desired.

Industry/Entity Type

Business

Contact Information for Business Card

My information is:
Theodore M. Quill, Attorney at Law
785 Birch Avenue Suite 300
Oakland, California 94719
Tel: (510) 384-6125
Fax: (510) 391-7802
email: neilquilllaw@mailvine.example
web: www.neilquilllaw.example

Font styles to use
Serif
Sans Serif
Decorative

Colors
0255a3
ffffff

Requirements
Must have
• Sharp lines, bold elements. Conservative use of colors, such as deep blues, burgundy, grays for example.
• While my logo says "Theodore M. Quill", it should be modified to show "Theodore M. Quill".
Should not have
• Cliche imagery such as scales of justice, gavels, Statue of Liberty, etc.

```html
<!DOCTYPE html>
<html lang="en">
<head>
<meta charset="utf-8">
<title>Theodore M. Quill — Business Card</title>
<link rel="stylesheet" href="https://fonts.googleapis.com/css2?family=Montserrat:wght@400;500;600&display=swap">
<style>
  :root {
    --navy: #1f4b63;
    --navy-deep: #163a4e;
    --ink: #2a2f33;
    --muted: #5d6468;
    --silver: #b9bec2;
    --card: #fdfdfd;
    --backdrop: #e7e8e9;
  }
  html, body {
    margin: 0;
    width: 1200px;
    height: 899px;
    overflow: hidden;
    background: var(--backdrop);
    font-family: "Montserrat", Arial, sans-serif;
  }
  .business-card {
    position: absolute;
    left: 100px;
    top: 164px;
    width: 1000px;
    height: 572px;
    border-radius: 56px;
    background: var(--card);
    overflow: hidden;
    box-shadow: 0 10px 30px rgba(0,0,0,0.12);
  }
  .wave-band {
    position: absolute;
    inset: 0;
    width: 1000px;
    height: 572px;
  }
  .brand-lockup {
    position: absolute;
    left: 56px;
    top: 196px;
    width: 440px;
    display: flex;
    align-items: center;
    gap: 14px;
  }
  .brand-mark {
    width: 40px;
    height: 40px;
    border-radius: 50%;
    background: var(--navy);
    flex: none;
  }
  .brand-name {
    font-weight: 600;
    font-size: 28px;
    letter-spacing: 1px;
    color: var(--navy);
    text-transform: uppercase;
    white-space: nowrap;
  }
  .contact-block {
    position: absolute;
    left: 540px;
    top: 104px;
    color: var(--ink);
  }
  .person-name {
    margin: 0;
    font-size: 26px;
    font-weight: 500;
    letter-spacing: 2px;
    color: var(--navy);
  }
  .person-title {
    margin: 4px 0 0;
    font-size: 17px;
    color: var(--muted);
  }
  .office-address {
    margin: 30px 0 0;
    font-style: normal;
    font-size: 18px;
    line-height: 1.3;
    color: var(--ink);
  }
  .contact-list {
    list-style: none;
    padding: 0;
    margin: 26px 0 0;
  }
  .contact-list li {
    display: flex;
    align-items: center;
    gap: 12px;
    height: 26px;
    font-size: 14px;
    color: var(--muted);
  }
  .contact-icon {
    width: 15px;
    height: 15px;
    fill: var(--navy);
    flex: none;
  }
  .band-website {
    position: absolute;
    right: 70px;
    bottom: 34px;
    margin: 0;
    font-size: 20px;
    letter-spacing: 3px;
    color: #ffffff;
  }
</style>
</head>
<body>
  <article class="business-card">
    <svg class="wave-band" viewBox="0 0 1000 572" aria-hidden="true">
      <defs>
        <linearGradient id="silverSweep" x1="0" x2="1" y1="0" y2="0">
          <stop offset="0" stop-color="#eceeef"/>
          <stop offset="0.5" stop-color="#9da3a7"/>
          <stop offset="1" stop-color="#e2e4e5"/>
        </linearGradient>
        <linearGradient id="navyFill" x1="0" x2="1" y1="0" y2="0">
          <stop offset="0" stop-color="#1f4b63"/>
          <stop offset="1" stop-color="#163a4e"/>
        </linearGradient>
      </defs>
      <path d="M0 332 C 260 400, 600 450, 1000 452 L1000 470 C 600 470, 260 430, 0 370 Z" fill="url(#silverSweep)"/>
      <path d="M0 385 C 240 440, 560 478, 1000 478 L1000 572 L0 572 Z" fill="url(#navyFill)"/>
    </svg>

    <div class="brand-lockup">
      <span class="brand-mark"></span>
      <span class="brand-name">Theodore M. Quill</span>
    </div>

    <section class="contact-block">
      <h1 class="person-name">THEODORE M. QUILL</h1>
      <p class="person-title">Attorney at Law</p>
      <address class="office-address">785 Birch Avenue Suite 300<br>Oakland, California 94719</address>
      <ul class="contact-list">
        <li>
          <svg class="contact-icon" viewBox="0 0 16 16"><path d="M3 1h3l1.5 4-2 1.2a9 9 0 0 0 4.3 4.3L11 8.5 15 10v3a2 2 0 0 1-2 2A12 12 0 0 1 1 3a2 2 0 0 1 2-2z"/></svg>
          (510) 384-6125
        </li>
        <li>
          <svg class="contact-icon" viewBox="0 0 16 16"><path d="M4.5 0h7A1.5 1.5 0 0 1 13 1.5v13a1.5 1.5 0 0 1-1.5 1.5h-7A1.5 1.5 0 0 1 3 14.5v-13A1.5 1.5 0 0 1 4.5 0zM5 2v10h6V2zm3 11a1 1 0 1 0 0 2 1 1 0 0 0 0-2z"/></svg>
          (510) 384-6190
        </li>
        <li>
          <svg class="contact-icon" viewBox="0 0 16 16"><path d="M4 1h8v4H4zM2 6h12a2 2 0 0 1 2 2v5h-3v2H3v-2H0V8a2 2 0 0 1 2-2zm3 5v3h6v-3z"/></svg>
          (510) 391-7802
        </li>
        <li>
          <svg class="contact-icon" viewBox="0 0 16 16"><path d="M1 3h14v10H1zm1.5 1.2V5l5.5 4 5.5-4v-.8L8 8z"/></svg>
          neilquilllaw@mailvine.example
        </li>
        <li>
          <svg class="contact-icon" viewBox="0 0 16 16"><path d="M8 0a8 8 0 1 0 0 16A8 8 0 0 0 8 0zm0 1.5c.9 0 2 1.9 2.3 5H5.7C6 3.4 7.1 1.5 8 1.5zM1.6 7.5h2.6c.1-2 .6-3.8 1.4-5A6.5 6.5 0 0 0 1.6 7.5zm0 1a6.5 6.5 0 0 0 4 5c-.8-1.2-1.3-3-1.4-5zm4.1 0c.2 3.1 1.4 6 2.3 6s2.1-2.9 2.3-6zm6.1 0c-.1 2-.6 3.8-1.4 5a6.5 6.5 0 0 0 4-5zm2.6-1a6.5 6.5 0 0 0-4-5c.8 1.2 1.3 3 1.4 5z"/></svg>
          www.neilquilllaw.example
        </li>
      </ul>
    </section>

    <p class="band-website">www.neilquilllaw.example</p>
  </article>
</body>
</html>
```